A Techincal Author needs a site to promote his Programming Books

The StudyAlong series is a collection of books focusing on building the same app with different technologies. The purpose of this project is to design a web site home page that can be used to sell the books.

Expected Deliverables
• StudyAlong Logo as Illustrator file
• Master graphic design files for any relevant web assets
• HTML and CSS for home page, if applicable

Target Market(s)

The target market for our series is web programmers. They are people who have some experience, but want to learn a new tool. Programmers are analytical, logical people who like structure in the things they do.

Here are some things our customers like:

• Chirply / Postbox
• Crown of Ashes / Hollow Tide / Salt Hollow
• SmartPhones, Tablets, Stridelets, and other tech gadgets.

The design should try to speak to that market.

Requirements
Must have
• The primary tasks for this project are:
• 1) Create "Study Along" Logo.
• * All “NetPivot” properties use a similar logo approach, with the NetPivot ball icon on the left, a reflection below it. The company name is on the right, roughly the same size as the ball icon. A tag line underneath the company name, roughly the same size as the reflection.
• * Company Name: Study Along
• * Tagline: Knowledge to Boost Your Career
• * Logo color is up to the discretion of the designer, but should be compatible with the site design.
• * Sample Logos for other NetPivot properties in Illustrator format are available as attachments to this project.
• 2) Design the Study Along Home Page.
• The home page should follow this format:
• * Logo
• * Nav Bar
• • Buy (The Home Page)
• • About
• • Contact
• * Main Content
• • Home page content detailed in attachment
• * Footer
• • Copyright notice
• • Links to other stuff we do ( net-pivot.example | marlonpeake.example | BeyondTheGrid.example )
Nice to have
• It would be nice to have a book as part of the home page content.
Should not have
• Please do not use the same color scheme as BeyondTheGrid.example or Plumvane.example or QueryTheMaven.example

```html
<!DOCTYPE html>
<html lang="en">
<head>
<meta charset="utf-8">
<title>Study Along — Programming Books</title>
<link rel="stylesheet" href="https://fonts.googleapis.com/css2?family=Raleway:wght@400;500;700&family=Open+Sans:ital,wght@0,400;1,400&family=Hind:wght@600&display=swap">
<style>
:root{
  --red:#e0313f;
  --gold:#f5b800;
  --ink:#444;
  --muted:#777;
  --topbar:#e5e5e5;
  --row-a:#f4f4f4;
  --row-b:#ececec;
  --cell-line:#ffffff;
  --blue:#0d5fd1;
  --blue-dark:#0a3f9a;
  --orange:#ff9a00;
  --footer:#f8f8f8;
}
*{margin:0;padding:0;box-sizing:border-box}
html,body{width:894px;height:1200px;overflow:hidden;background:#fff}
body{position:relative;font-family:"Raleway",sans-serif;color:var(--ink)}
.topbar{position:absolute;left:0;top:0;width:894px;height:23px;background:var(--topbar);
  font-family:"Open Sans",sans-serif;font-style:italic;font-size:10px;color:#555;text-align:right;padding:5px 60px 0 0}
.brand{position:absolute;left:63px;top:38px;display:flex;flex-direction:column;align-items:flex-start;gap:10px}
.brand-mark{width:50px;height:46px;background:#1d8fd1;margin-left:30px}
.brand-name{font-family:"Raleway",sans-serif;font-weight:700;font-size:15px;color:var(--red);letter-spacing:.5px}
.nav{position:absolute;left:0;top:133px;width:894px;height:40px;background:var(--red)}
.nav a{position:absolute;top:12px;color:#fff;text-decoration:none;font-size:13px;font-weight:500}
.hero{position:absolute;left:0;top:173px;width:894px;height:316px;
  background:radial-gradient(ellipse at 30% 40%,#d9a585 0%,#a8604a 35%,#5a2a22 70%,#3a1a18 100%)}
.hero-title{position:absolute;left:431px;top:76px;font-family:"Hind",sans-serif;font-weight:600;font-size:38px;line-height:40px;color:#fff;letter-spacing:.5px}
.hero-title .accent{color:var(--gold)}
.section-title{position:absolute;left:0;width:894px;text-align:center;font-size:21px;font-weight:400;color:#444}
.rule{position:absolute;height:1px;background:#999}
.intro{position:absolute;left:55px;top:562px;width:784px;text-align:center;font-size:11px;line-height:20.7px;color:var(--muted)}
.tab{position:absolute;top:764px;width:196px;height:41px;background:var(--red);color:#fff;font-size:14.5px;padding-top:11px}
.tab-left{padding-left:12px}
.tab-center{text-align:center}
.tab-pointer{position:absolute;left:140px;top:805px;width:0;height:0;border-left:9px solid transparent;border-right:9px solid transparent;border-top:9px solid var(--red)}
.products{position:absolute;left:57px;top:819px;width:788px;height:206px;border:1px solid #ddd;padding:2px 3px}
.product-row{display:flex;height:50px;background:var(--row-a);border-bottom:1px solid var(--cell-line)}
.product-row:nth-child(even){background:var(--row-b)}
.product-row > div{display:flex;align-items:center;border-right:2px solid var(--cell-line);font-size:11.5px;color:#666}
.cell-name{width:173px;padding-left:17px}
.cell-price{width:94px;justify-content:center}
.cell-buy{width:133px;justify-content:center}
.cell-store{flex:1;padding-left:36px;border-right:none!important}
.btn-buy{width:94px;height:26px;border-radius:13px;background:linear-gradient(#1a78e6,var(--blue));border:2px solid var(--blue-dark);color:#fff;font-size:10.5px;display:flex;align-items:center;justify-content:center}
.btn-store{width:117px;height:34px;border-radius:2px;background:var(--orange);color:#fff;font-size:14px;font-weight:500;display:flex;align-items:center;justify-content:center}
.footer{position:absolute;left:0;top:1093px;width:894px;height:107px;background:var(--footer);border-top:1px solid #ddd;font-family:"Open Sans",sans-serif}
.partners-label{position:absolute;left:60px;top:18px;font-size:11px;color:#333}
.partner-badge{position:absolute;left:59px;top:37px;width:235px;height:47px;background:#fff;border:1px solid #ccc}
.copyright{position:absolute;right:52px;top:47px;font-size:11px;color:#333}
</style>
</head>
<body>
  <div class="topbar">Call us&nbsp; 1-800-555-0147</div>

  <div class="brand">
    <div class="brand-mark"></div>
    <div class="brand-name">STUDY - ALONG</div>
  </div>

  <nav class="nav">
    <a style="left:260px">HOME</a>
    <a style="left:350px">BUY</a>
    <a style="left:428px">ABOUT US</a>
    <a style="left:541px">CONTACT US</a>
  </nav>

  <header class="hero" role="img" aria-label="Photo of hands holding a tablet in warm light">
    <h1 class="hero-title">KNOWLEDGE TO BOOST<br><span class="accent">YOUR CAREER</span></h1>
  </header>

  <h2 class="section-title" style="top:512px">Welcome to Study Along</h2>
  <div class="rule" style="left:350px;top:544px;width:165px"></div>
  <p class="intro">Lorem ipsum dolor sit amet, consectetuer adipiscing elit. Aenean commodo ligula eget dolor. Aenean massa. Cum sociis&nbsp; natoque penatibus et magnis<br>Lorem ipsum dolor sit amet, consectetuer adipiscing elit. Aenean commodo ligula eget&nbsp; dolor. Aenean massa. Cum sociis natoque<br>penatibus et magnisdolor sit amet, consectetuer adipiscing elit&nbsp;&nbsp; Aenean commodo ligula eget dolor. Aenean massa. Cum socii<br>natoque penatibus et magnis dolor sit amet consectetuer adipiscing elit.Aenean commodo ligula eget dolor. Aenean massa.<br>Cum sociis natoque penatibus et magnis .</p>

  <h2 class="section-title" style="top:698px">Our Products</h2>
  <div class="rule" style="left:397px;top:730px;width:79px"></div>

  <div class="tab tab-left" style="left:58px">NgScript 1.5 &amp; Strapline</div>
  <div class="tab tab-left" style="left:267px">NgScript 2 &amp; Strapline</div>
  <div class="tab tab-center" style="left:478px">ReactiveKit</div>
  <div class="tab-pointer"></div>

  <div class="products">
    <div class="product-row">
      <div class="cell-name">With Mock Services</div>
      <div class="cell-price">$5.99</div>
      <div class="cell-buy"><span class="btn-buy">BUY FROM US</span></div>
      <div class="cell-store"><span class="btn-store">Shopvane</span></div>
    </div>
    <div class="product-row">
      <div class="cell-name">With NodeRun Services</div>
      <div class="cell-price">$5.99</div>
      <div class="cell-buy"><span class="btn-buy">BUY FROM US</span></div>
      <div class="cell-store"><span class="btn-store">Shopvane</span></div>
    </div>
    <div class="product-row">
      <div class="cell-name">With FrostForge Services</div>
      <div class="cell-price">$5.99</div>
      <div class="cell-buy"><span class="btn-buy">BUY FROM US</span></div>
      <div class="cell-store"><span class="btn-store">Shopvane</span></div>
    </div>
    <div class="product-row">
      <div class="cell-name">Buy Them All</div>
      <div class="cell-price">$9.99</div>
      <div class="cell-buy"><span class="btn-buy">BUY FROM US</span></div>
      <div class="cell-store"><span class="btn-store">Shopvane</span></div>
    </div>
  </div>

  <footer class="footer">
    <div class="partners-label">Partners</div>
    <div class="partner-badge" aria-label="Partner badge"></div>
    <div class="copyright">2016@study-along.example. All Rights Reserved.</div>
  </footer>
</body>
</html>
```